Executive Taxi firm with Chauffeur service Website

I have my domain name registered and I have started to work on my site but I am struggling. I am just about to get a logo for the company and need a web site that clearly represents the fact we are an executive/luxury brand in private hire vehicles. We offer airport transfers, train station transfers, seaport transfers, holiday transfers and business to business pick up and drop off.

Target Market(s)

Corporate people, holidaymakers looking for a luxury start their holiday. VIPs' and celebrities.

Number of Pages Required

5+ page

Font styles to use
Serif
Sans Serif
Decorative
Script

Colors

Designer to choose colors to be used in the design.

Requirements
Must have
• Home Page, Services, About Us, VIP and Contact us
• Please see www.brivomotors.co.uk I have started it but not happy with it at all.
Nice to have
• Booking form or enquiry form.

```html
<!DOCTYPE html>
<html lang="en">
<head>
<meta charset="utf-8">
<title>Brivo Motors – Executive Taxi &amp; Chauffeur</title>
<link href="https://fonts.googleapis.com/css2?family=Lato:ital,wght@0,400;0,700;0,900;1,700&display=swap" rel="stylesheet">
<style>
:root{
  --yellow:#f2c300;
  --yellow-deep:#e0b000;
  --ink:#111111;
  --dark:#1b1b1b;
  --grey-text:#555555;
  --light:#f1f1f1;
  --white:#ffffff;
}
*{box-sizing:border-box;margin:0;padding:0}
html,body{width:1200px;height:3822px;overflow:hidden}
body{font-family:'Lato',sans-serif;color:var(--ink);background:var(--white);position:relative}
.abs{position:absolute}
a{color:inherit;text-decoration:none}

/* hero */
.hero{left:0;top:0;width:1200px;height:880px;background:linear-gradient(120deg,#3a3a38 0%,#24231f 45%,#121212 100%)}
.hero-photo{left:560px;top:160px;width:520px;height:620px;border-radius:40px;background:radial-gradient(ellipse at 50% 40%,rgba(120,120,115,.45),rgba(20,20,20,0) 70%)}
.brand{display:flex;align-items:center;gap:14px;color:var(--white);font-weight:900;font-size:30px;letter-spacing:2px;text-transform:uppercase}
.brand-dot{width:22px;height:22px;border-radius:50%;background:var(--yellow)}
.call{right:112px;top:36px;color:var(--yellow);font-weight:700;font-style:italic;font-size:21px;display:flex;align-items:center;gap:8px}
.nav{right:112px;top:92px;display:flex;gap:40px;font-size:14px;font-weight:700;color:var(--white);align-items:center}
.nav .active{color:var(--yellow)}
.slider-dots{left:1134px;top:330px;display:flex;flex-direction:column;gap:20px}
.slider-dots span{width:12px;height:12px;border-radius:50%;border:2px solid var(--white)}
.slider-dots span.on{background:var(--yellow);border-color:var(--yellow)}

.booking{left:112px;top:200px;width:456px;height:400px;background:#f4f4f4;border-radius:3px;padding:42px 28px 0}
.booking h2{text-align:center;font-size:30px;font-weight:900;color:var(--ink)}
.booking h2 em{font-style:normal;color:var(--yellow)}
.vehicles{display:flex;justify-content:space-between;margin:24px 6px 0}
.vehicle{width:82px;text-align:center;font-size:10px;font-weight:700}
.vehicle .ring{width:82px;height:82px;border-radius:50%;border:2px solid #d6d6d6;background:var(--white);display:flex;align-items:center;justify-content:center;margin-bottom:8px}
.vehicle.on .ring{background:var(--yellow);border-color:var(--yellow)}
.fields{display:grid;gap:14px;margin-top:36px}
.row2{display:grid;grid-template-columns:1fr 1fr;gap:14px}
.row3{display:grid;grid-template-columns:1fr 1fr 1fr;gap:12px}
.field{height:34px;background:var(--white);border:1px solid #dadada;font-size:11px;color:#444;display:flex;align-items:center;justify-content:space-between;padding:0 12px}
.field svg{width:12px;height:12px}
.btn{display:inline-flex;align-items:center;gap:10px;height:42px;padding:0 24px;border-radius:21px;font-size:13px;font-weight:900;text-transform:uppercase}
.btn i{width:14px;height:14px;border-radius:50%;display:inline-flex;align-items:center;justify-content:center;font-style:normal;font-size:9px}
.btn-yellow{background:var(--yellow);color:var(--ink)}
.btn-yellow i{background:var(--ink);color:var(--yellow)}
.btn-dark{background:var(--ink);color:var(--white)}
.btn-dark i{background:var(--white);color:var(--ink)}
.booking .btn{position:absolute;left:155px;top:380px}

/* headings */
.title{font-size:48px;font-weight:900;letter-spacing:1px;text-transform:uppercase}
.title em{font-style:normal;color:var(--yellow)}
.body-text{font-size:14px;line-height:32px;color:var(--grey-text)}

/* about */
.about{left:112px;top:960px;width:470px}
.about h3{font-size:26px;font-weight:700;margin-top:28px}
.about h4{font-size:23px;font-weight:400;color:var(--yellow);margin-top:6px}
.about .body-text{margin-top:18px}
.about .actions{display:flex;gap:10px;margin-top:24px}
.car-art{left:600px;top:940px;width:530px;height:430px;border-radius:50% 50% 40% 40%/40% 40% 30% 30%;background:radial-gradient(ellipse at 50% 40%,#ffd21a 0%,#f0c000 40%,rgba(240,240,240,.6) 75%,rgba(255,255,255,0) 100%)}

/* services */
.services{left:0;top:1430px;width:1200px;height:622px;background:linear-gradient(180deg,#f3c800,#e4b400)}
.services .title{position:absolute;top:70px;width:100%;text-align:center;color:var(--white)}
.services .title em{color:var(--ink)}
.service{position:absolute;top:180px;width:300px;text-align:center}
.service svg{display:block;margin:0 auto}
.service h5{font-size:21px;font-weight:700;margin-top:30px;color:var(--ink)}
.service p{font-size:13px;line-height:30px;color:#3a3000;margin-top:12px}
.service .more{display:block;font-size:13px;font-weight:700;margin-top:14px}

/* clients */
.clients{left:0;top:2052px;width:1200px;height:610px;background:var(--light)}
.clients .title{position:absolute;top:100px;width:100%;text-align:center}
.card{position:absolute;top:213px;width:302px;height:245px;background:var(--white);text-align:center}
.card p{position:absolute;left:0;top:24px;width:100%;font-size:12px;line-height:31px;color:var(--grey-text);white-space:nowrap}
.card .quote{position:absolute;left:0;top:130px;width:100%;font-size:52px;font-weight:900;color:var(--yellow);line-height:40px;height:30px;overflow:hidden}
.card .name{position:absolute;left:0;top:168px;width:100%;font-size:18px;font-weight:900;line-height:22px}
.avatar{position:absolute;left:115px;bottom:-36px;width:72px;height:72px;border-radius:50%;background:#c9c9c9;border:4px solid var(--white)}
.arrow{position:absolute;top:2368px;width:38px;height:38px;border-radius:50%;background:var(--white);border:1px solid #cfcfcf;display:flex;align-items:center;justify-content:center}

/* always */
.always{left:112px;top:2780px;width:500px}
.always .title{line-height:64px}
.always .body-text{margin-top:22px;line-height:38px;font-size:13px}
.always .actions{display:flex;gap:10px;margin-top:28px}
.phone-art{left:690px;top:2730px;width:380px;height:500px;border-radius:50%;background:radial-gradient(circle at 50% 50%,#f2f2f2 0%,#dcdcdc 35%,#f2c300 36%,#1a1a1a 62%,rgba(255,255,255,0) 63%)}

/* footer */
.footer{left:0;top:3230px;width:1200px;height:592px;background:var(--ink)}
.footer .brand{position:absolute;left:112px;top:280px}
.contact{position:absolute;left:112px;top:350px;color:var(--white);font-size:14px;display:grid;gap:18px}
.contact div{display:flex;align-items:center;gap:16px}
.socials{position:absolute;left:112px;top:430px;display:flex;gap:26px}
.socials span{width:14px;height:14px;border-radius:50%;background:var(--yellow)}
.footer h6{position:absolute;font-size:16px;font-weight:700;color:var(--yellow);text-transform:uppercase}
.links{position:absolute;left:500px;top:315px;color:var(--white);font-size:13px;display:grid;gap:18px}
.news-text{position:absolute;left:695px;top:308px;color:var(--white);font-size:13px}
.news{position:absolute;left:695px;top:352px;display:flex}
.news .input{width:287px;height:38px;background:var(--white);font-size:12px;color:#777;padding:12px}
.news .submit{width:100px;height:38px;background:var(--yellow);font-size:14px;font-weight:900;display:flex;align-items:center;justify-content:center;margin-left:6px}
.copyright{position:absolute;top:548px;width:100%;text-align:center;color:var(--white);font-size:12px}
</style>
</head>
<body>

<section class="abs hero" aria-label="Welcome">
  <div class="abs hero-photo" role="img" aria-label="Photo of a hand holding a phone with a taxi booking app at night"></div>
  <div class="abs" style="left:112px;top:64px"><div class="brand"><span class="brand-dot"></span>Brivo Motors</div></div>
  <div class="abs call">
    <svg width="18" height="18" viewBox="0 0 24 24"><path fill="#f2c300" d="M6.6 10.8a15 15 0 0 0 6.6 6.6l2.2-2.2c.3-.3.7-.4 1-.2 1.1.4 2.3.6 3.6.6.6 0 1 .4 1 1V20c0 .6-.4 1-1 1A17 17 0 0 1 3 4c0-.6.4-1 1-1h3.5c.6 0 1 .4 1 1 0 1.3.2 2.5.6 3.6.1.3 0 .7-.2 1z"/></svg>
    CALL US : 07000 481629
  </div>
  <nav class="abs nav">
    <a class="active">HOME</a><a>SERVICES</a><a>ABOUT US</a><a>VIP</a><a>CONTACT US</a>
    <svg width="14" height="14" viewBox="0 0 24 24"><circle cx="10" cy="10" r="7" fill="none" stroke="#f2c300" stroke-width="3"/><path d="M15 15l6 6" stroke="#f2c300" stroke-width="3"/></svg>
  </nav>
  <div class="abs slider-dots"><span class="on"></span><span></span><span></span><span></span><span></span></div>

  <form class="abs booking">
    <h2>GET TAXI <em>ONLINE</em></h2>
    <div class="vehicles">
      <div class="vehicle on"><div class="ring"><svg width="50" height="26" viewBox="0 0 50 26"><path d="M4 18v-5l6-2 6-7h16l8 7 6 2v5z" fill="#111"/><circle cx="13" cy="19" r="4" fill="#111" stroke="#f2c300" stroke-width="2"/><circle cx="37" cy="19" r="4" fill="#111" stroke="#f2c300" stroke-width="2"/></svg></div>TAXI</div>
      <div class="vehicle"><div class="ring"><svg width="50" height="26" viewBox="0 0 50 26"><path d="M4 18v-5l6-2 6-7h16l8 7 6 2v5z" fill="none" stroke="#111" stroke-width="2"/><circle cx="13" cy="19" r="4" fill="#fff" stroke="#111" stroke-width="2"/><circle cx="37" cy="19" r="4" fill="#fff" stroke="#111" stroke-width="2"/></svg></div>BUSINESS</div>
      <div class="vehicle"><div class="ring"><svg width="50" height="26" viewBox="0 0 50 26"><path d="M3 18v-4l8-3 7-6h14l8 6 7 3v4z" fill="none" stroke="#111" stroke-width="2"/><circle cx="13" cy="19" r="4" fill="#fff" stroke="#111" stroke-width="2"/><circle cx="37" cy="19" r="4" fill="#fff" stroke="#111" stroke-width="2"/></svg></div>VIP</div>
      <div class="vehicle"><div class="ring"><svg width="50" height="26" viewBox="0 0 50 26"><path d="M4 18v-5l8-2 5-6h15l6 6 8 2v5z" fill="#111"/><circle cx="13" cy="19" r="4" fill="#fff" stroke="#111" stroke-width="2"/><circle cx="37" cy="19" r="4" fill="#fff" stroke="#111" stroke-width="2"/></svg></div>STANDARD</div>
    </div>
    <div class="fields">
      <div class="row2">
        <div class="field">From Address<svg viewBox="0 0 24 24"><path d="M12 2a7 7 0 0 0-7 7c0 5 7 13 7 13s7-8 7-13a7 7 0 0 0-7-7z" fill="#888"/></svg></div>
        <div class="field">To<svg viewBox="0 0 24 24"><path d="M12 2a7 7 0 0 0-7 7c0 5 7 13 7 13s7-8 7-13a7 7 0 0 0-7-7z" fill="#888"/></svg></div>
      </div>
      <div class="row3">
        <div class="field">Phone<svg viewBox="0 0 24 24"><path fill="#888" d="M6.6 10.8a15 15 0 0 0 6.6 6.6l2.2-2.2c.3-.3.7-.4 1-.2 1.1.4 2.3.6 3.6.6.6 0 1 .4 1 1V20c0 .6-.4 1-1 1A17 17 0 0 1 3 4c0-.6.4-1 1-1h3.5c.6 0 1 .4 1 1 0 1.3.2 2.5.6 3.6.1.3 0 .7-.2 1z"/></svg></div>
        <div class="field">Date<svg viewBox="0 0 24 24"><rect x="3" y="5" width="18" height="16" fill="none" stroke="#888" stroke-width="2"/><path d="M3 10h18" stroke="#888" stroke-width="2"/></svg></div>
        <div class="field">Time<svg viewBox="0 0 24 24"><circle cx="12" cy="12" r="9" fill="none" stroke="#888" stroke-width="2"/><path d="M12 7v5l3 2" stroke="#888" stroke-width="2" fill="none"/></svg></div>
      </div>
    </div>
    <a class="btn btn-yellow">GET TAXI <i>›</i></a>
  </form>
</section>

<svg class="abs" style="left:0;top:730px" width="1200" height="160" viewBox="0 0 1200 160" preserveAspectRatio="none" aria-hidden="true">
  <path d="M0 110 C 200 40, 420 20, 620 80 S 1000 140, 1200 40 L1200 160 L0 160 Z" fill="#000"/>
  <path d="M0 140 C 220 70, 430 55, 630 110 S 1000 160, 1200 80 L1200 160 L0 160 Z" fill="#fff"/>
</svg>

<section class="abs about">
  <h2 class="title">ABOUT <em>US</em></h2>
  <h3>We've been in the transport industry</h3>
  <h4>for &nbsp;over 60 years</h4>
  <p class="body-text">That's 60 years of history and business 'know how'.<br>Being one of the very first car transporters in the area we have now changed our expertise to transporting people throughout the UK and Europe.</p>
  <div class="actions"><a class="btn btn-yellow">READ MORE <i>›</i></a><a class="btn btn-dark">GET TAXI <i>›</i></a></div>
</section>
<div class="abs car-art" role="img" aria-label="Yellow taxi car with reflection"></div>

<section class="abs services">
  <h2 class="title">OUR <em>SERVICES</em></h2>
  <div class="service" style="left:90px">
    <svg width="150" height="210" viewBox="0 0 150 210"><path d="M75 4a71 71 0 0 0-71 71c0 50 71 131 71 131s71-81 71-131A71 71 0 0 0 75 4z" fill="#111"/><circle cx="75" cy="75" r="48" fill="none" stroke="#f2c300" stroke-width="3"/><circle cx="75" cy="75" r="40" fill="#fff"/><circle cx="75" cy="75" r="34" fill="#111"/><rect x="60" y="62" width="30" height="20" rx="2" fill="#f2c300"/><rect x="70" y="84" width="10" height="5" fill="#f2c300"/></svg>
    <h5>Allport Transfers</h5>
    <p>Airport and Seaport transfers are a particular<br>speciality of ours. We have in depth</p>
    <a class="more">Read More »</a>
  </div>
  <div class="service" style="left:450px">
    <svg width="150" height="210" viewBox="0 0 150 210"><path d="M75 4a71 71 0 0 0-71 71c0 50 71 131 71 131s71-81 71-131A71 71 0 0 0 75 4z" fill="#111"/><circle cx="75" cy="75" r="48" fill="none" stroke="#f2c300" stroke-width="3"/><circle cx="75" cy="75" r="40" fill="#fff"/><circle cx="75" cy="75" r="34" fill="#111"/><circle cx="75" cy="67" r="8" fill="#f2c300"/><path d="M60 90a15 13 0 0 1 30 0z" fill="#f2c300"/></svg>
    <h5>Business to Business Transfers</h5>
    <p>If its a stress free chauffeur service you need<br>then look no further. A selection</p>
    <a class="more">Read More »</a>
  </div>
  <div class="service" style="left:810px">
    <svg width="150" height="210" viewBox="0 0 150 210"><path d="M75 4a71 71 0 0 0-71 71c0 50 71 131 71 131s71-81 71-131A71 71 0 0 0 75 4z" fill="#111"/><circle cx="75" cy="75" r="48" fill="none" stroke="#f2c300" stroke-width="3"/><circle cx="75" cy="75" r="40" fill="#fff"/><circle cx="75" cy="75" r="34" fill="#111"/><rect x="59" y="65" width="32" height="22" rx="2" fill="#f2c300"/><rect x="68" y="59" width="14" height="6" fill="none" stroke="#f2c300" stroke-width="2"/></svg>
    <h5>Holiday Transfers</h5>
    <p>Why not start your holiday off stress free and<br>allow us to take care of your outbound</p>
    <a class="more">Read More »</a>
  </div>
</section>

<section class="abs clients">
  <h2 class="title">CLIENTS <em>SAY</em></h2>
  <div class="card" style="left:115px"><p>Sed ut perspiciatis unde omnis iste natus error<br>sit voluptatem accusantium doloremque lau-<br>dantiumotam rem aperiaaque ipsa</p><div class="quote">“</div><div class="name">JOHN DOE</div><div class="avatar" role="img" aria-label="Client portrait"></div></div>
  <div class="card" style="left:450px"><p>Sed ut perspiciatis unde omnis iste natus error<br>sit voluptatem accusantium doloremque lau-<br>dantiumotam rem aperiaaque ipsa</p><div class="quote">“</div><div class="name">JOHN DOE</div><div class="avatar" role="img" aria-label="Client portrait"></div></div>
  <div class="card" style="left:784px"><p>Sed ut perspiciatis unde omnis iste natus error<br>sit voluptatem accusantium doloremque lau-<br>dantiumotam rem aperiaaque ipsa</p><div class="quote">“</div><div class="name">JOHN DOE</div><div class="avatar" role="img" aria-label="Client portrait"></div></div>
</section>
<div class="arrow" style="left:57px"><svg width="10" height="12" viewBox="0 0 10 12"><path d="M7 1L2 6l5 5" fill="none" stroke="#111" stroke-width="2"/></svg></div>
<div class="arrow" style="left:1104px"><svg width="10" height="12" viewBox="0 0 10 12"><path d="M3 1l5 5-5 5" fill="none" stroke="#111" stroke-width="2"/></svg></div>

<section class="abs always">
  <h2 class="title">ALWAYS <em>HERE<br>FOR YOU</em></h2>
  <p class="body-text">We provide airport transfers to and from all major UK airports, seaports, train station transfers and an executive business to business transfer service. Whether you have an individual or group transfer request, our company-owned fleet offers a choice of options to suit your needs, from luxury saloons</p>
  <div class="actions"><a class="btn btn-yellow">READ MORE <i>›</i></a><a class="btn btn-dark">GET DIRECTIONS <i>›</i></a></div>
</section>
<div class="abs phone-art" role="img" aria-label="Smartphone showing the taxi booking app map"></div>

<footer class="abs footer">
  <svg class="abs" style="left:0;top:-20px" width="1200" height="230" viewBox="0 0 1200 230" preserveAspectRatio="none" aria-hidden="true">
    <path d="M0 0 L1200 0 L1200 60 C 1000 160, 780 150, 580 90 S 180 80, 0 150 Z" fill="#fff"/>
  </svg>
  <div class="brand"><span class="brand-dot"></span>Brivo Motors</div>
  <div class="contact">
    <div><svg width="14" height="14" viewBox="0 0 24 24"><path fill="#f2c300" d="M6.6 10.8a15 15 0 0 0 6.6 6.6l2.2-2.2c.3-.3.7-.4 1-.2 1.1.4 2.3.6 3.6.6.6 0 1 .4 1 1V20c0 .6-.4 1-1 1A17 17 0 0 1 3 4c0-.6.4-1 1-1h3.5c.6 0 1 .4 1 1 0 1.3.2 2.5.6 3.6.1.3 0 .7-.2 1z"/></svg>07000 481629</div>
    <div><svg width="14" height="12" viewBox="0 0 24 18"><rect width="24" height="18" fill="#f2c300"/><path d="M0 0l12 9 12-9" fill="none" stroke="#111" stroke-width="2"/></svg>info@brivomotors.co.uk</div>
  </div>
  <div class="socials"><span></span><span></span><span></span><span></span><span></span></div>
  <h6 style="left:500px;top:275px">Quick Links</h6>
  <div class="links"><a>Home</a><a>Services</a><a>About Us</a><a>VIP</a><a>Contact us</a></div>
  <h6 style="left:695px;top:275px">Stay Connected</h6>
  <p class="news-text">Join our newsletter and find out more.</p>
  <div class="news"><div class="input">Enter Email</div><div class="submit">SUBMIT</div></div>
  <p class="copyright">© Copyright 2018 Companyname.All Rights Reserved</p>
</footer>

</body>
</html>
```